Meridale Staffing Website

My business has been word of mouth over the last 3 years and has grown. Now I need a website for additional marketing as we have new clients asking for a website.

You have already completed my Logo during an earlier project. I have attached the logo.

We do Staff Augmentation and Operation Support.

What is that?
Staff augmentation is an outsourcing strategy that allows companies to fill specific, temporary roles to achieve business objectives. This staffing method complements existing teams with specific talent, enhancing business capabilities or filling gaps left by members on extended leave.

We work alongside the internal recruiting team to assist clients to meet and exceed financial goals.

```html
<!DOCTYPE html>
<html lang="en">
<head>
<meta charset="utf-8">
<title>Meridale Staffing</title>
<link href="https://fonts.googleapis.com/css2?family=Poppins:ital,wght@0,300;0,400;0,500;0,600;0,700;0,800;1,400&display=swap" rel="stylesheet">
<style>
:root{
  --navy:#12446e;
  --navy-deep:#0f3a60;
  --ink:#3a3a3a;
  --muted:#777;
  --light:#f1f1f1;
  --white:#fff;
  --dark:#1e1e1e;
  --grey-btn:#6f6f6f;
  --lavender:#eceef8;
}
*{margin:0;padding:0;box-sizing:border-box}
html,body{width:1200px;height:3836px;overflow:hidden}
body{font-family:'Poppins',sans-serif;color:var(--ink);background:var(--white);position:relative}
.abs{position:absolute}
.center{left:0;width:1200px;text-align:center}

/* header */
.site-header{position:absolute;left:0;top:0;width:1200px;height:92px;background:var(--white)}
.brand{position:absolute;display:flex;align-items:center;gap:10px;font-weight:600;color:var(--navy);line-height:1}
.brand-dot{border-radius:50%;background:var(--navy)}
.brand-header{left:116px;top:18px}
.brand-header .brand-dot{width:52px;height:52px}
.brand-header .brand-name{font-size:25px;line-height:0.95}
.nav a{position:absolute;top:37px;font-size:15px;color:#444;text-decoration:none}
.nav a.active{color:var(--navy)}
.lang{position:absolute;left:978px;top:27px;width:109px;height:39px;border:1px solid var(--navy);font-size:13px;display:flex;align-items:center;justify-content:center;gap:6px;color:#333}
.flag{width:16px;height:10px;background:linear-gradient(#b22234 0 20%,#fff 20% 40%,#b22234 40% 60%,#fff 60% 80%,#b22234 80%);position:relative}
.flag::before{content:"";position:absolute;left:0;top:0;width:7px;height:6px;background:#3c3b6e}

/* hero */
.hero{position:absolute;left:0;top:92px;width:1200px;height:643px;background:linear-gradient(100deg,#1f4f78 0%,#2a5d88 45%,#1d4a73 100%)}
.hero h1{position:absolute;left:107px;top:198px;font-size:55px;font-weight:700;color:var(--white);letter-spacing:.5px}
.hero p{position:absolute;left:112px;top:268px;width:500px;font-size:16.5px;line-height:33.5px;color:var(--white)}
.btn-grey{position:absolute;left:112px;top:381px;width:181px;height:51px;background:var(--grey-btn);color:var(--white);font-size:16px;font-weight:500;display:flex;align-items:center;justify-content:center;gap:8px}
.scroll{position:absolute;left:585px;top:571px;width:30px;height:56px;border:2px solid rgba(255,255,255,.8);border-radius:15px}

/* sections */
.section-title{font-weight:800;color:var(--navy)}
.lede{font-size:16px;line-height:28.5px;color:#444}
.rule{position:absolute;left:578px;width:44px;height:3px;background:var(--navy)}
.btn-navy{position:absolute;left:522px;width:155px;height:52px;background:var(--navy);color:var(--white);font-size:15.5px;font-weight:600;display:flex;align-items:center;justify-content:center}

.welcome-body{font-size:13.5px;line-height:30px;color:var(--muted)}

.services-band{position:absolute;left:0;top:1251px;width:1200px;height:487px;background:var(--light)}
.tab-active{position:absolute;left:408px;top:1453px;width:193px;height:55px;border:1px solid #ccc;background:var(--white);font-size:15.5px;font-weight:500;color:var(--navy);display:flex;align-items:center;justify-content:center}
.tab{position:absolute;left:613px;top:1469px;font-size:15.5px;color:#888}
.svc-card{position:absolute;top:1563px;height:380px;background:var(--white);box-shadow:0 3px 10px rgba(0,0,0,.15);overflow:hidden}
.svc-photo{height:316px}
.svc-label{height:64px;background:var(--navy);color:var(--white);font-size:15px;font-weight:600;display:flex;align-items:center;justify-content:center}

.news-lead{position:absolute;left:110px;top:2202px;width:463px;height:581px;background:var(--white);box-shadow:0 2px 12px rgba(0,0,0,.15)}
.news-lead .photo{height:299px;background:linear-gradient(160deg,#4a4036,#2d2a26 60%,#514a40)}
.pill{background:var(--navy);color:var(--white);border-radius:0 20px 20px 0;font-size:14px;display:flex;align-items:center;padding-left:25px}
.news-title{color:var(--navy);font-weight:500}
.news-text{color:#666}
.read-more{color:var(--navy);font-weight:600;border-bottom:1.5px solid var(--navy);display:inline-block}
.news-item{position:absolute;left:600px;width:485px;height:270px;display:flex;box-shadow:0 2px 8px rgba(0,0,0,.12)}
.news-item .photo{width:231px;height:100%}
.news-item .body{flex:1;background:var(--lavender);position:relative;padding:78px 14px 0 13px}
.news-item .pill{position:absolute;left:0;top:22px;width:110px;height:30px;font-size:12.5px;padding-left:12px}
.news-item .news-title{font-size:13px;line-height:21.5px;font-weight:600}
.news-item .news-text{font-size:11.5px;line-height:25.5px;margin-top:10px}
.news-item .read-more{font-size:13px;margin:6px 0 0 4px}

.testimonials{position:absolute;left:0;top:2954px;width:1200px;height:474px;background:linear-gradient(180deg,#232323,#181818)}
.arrow{position:absolute;top:3180px;width:20px;height:30px}
.dots{position:absolute;left:505px;top:3345px;display:flex;gap:11px}
.dots span{width:9px;height:9px;border-radius:50%;background:#888}
.dots span:first-child{background:var(--white)}

.site-footer{position:absolute;left:0;top:3428px;width:1200px;height:408px;background:var(--navy-deep);color:var(--white)}
.brand-footer{left:113px;top:104px;color:var(--white)}
.brand-footer .brand-dot{width:72px;height:72px;background:var(--white)}
.brand-footer .brand-name{font-size:33px;line-height:1}
.social{position:absolute;top:3667px;width:30px;height:30px;border:1.5px solid var(--white);border-radius:50%}
.foot-col{position:absolute;top:3506px;font-size:15px}
.foot-col h4{font-weight:500;font-size:15.5px;display:inline-block;border-bottom:2px solid var(--white);padding-bottom:6px;margin-bottom:14px}
.foot-col li{list-style:none;line-height:25.8px;font-size:14.5px}
.foot-rule{position:absolute;left:112px;top:3748px;width:975px;height:1px;background:rgba(255,255,255,.2)}
</style>
</head>
<body>

<header class="site-header">
  <div class="brand brand-header"><span class="brand-dot"></span><span class="brand-name">MERIDALE<br>STAFFING</span></div>
  <nav class="nav">
    <a class="active" style="left:460px">Home</a>
    <a style="left:536px">About Us</a>
    <a style="left:634px">Services</a>
    <a style="left:728px">Blog</a>
    <a style="left:792px">Reviews</a>
    <a style="left:884px">Contact</a>
  </nav>
  <div class="lang"><span class="flag"></span>English ▾</div>
</header>

<section class="hero" role="img" aria-label="Business team in an office meeting, tinted blue">
  <h1>Meridale Staffing</h1>
  <p>Lorem ipsum dolor sit amet, consectetur adipiscing elit, sed do eiusmod tempor incididunt ut labore et dolore magna aliqua. Ut enim ad minim veniam,</p>
  <div class="btn-grey">Get Started
    <svg width="14" height="14" viewBox="0 0 14 14"><circle cx="7" cy="7" r="7" fill="#fff"/><path d="M6 4l3 3-3 3" stroke="#6f6f6f" stroke-width="2" fill="none"/></svg>
  </div>
  <div class="scroll"><svg width="26" height="52" viewBox="0 0 26 52"><path d="M9 24l4 4 4-4" stroke="#fff" stroke-width="1.8" fill="none"/></svg></div>
</section>

<section class="welcome">
  <h2 class="abs center section-title" style="top:810px;font-size:32px">Welcome to Meridale Staffing</h2>
  <p class="abs center lede" style="top:869px">Lorem ipsum dolor sit amet, consectetur adipiscing elit, sed do<br>eiusmod tempor incididunt ut labore et dolore</p>
  <div class="rule" style="top:937px"></div>
  <p class="abs center welcome-body" style="top:969px">Lorem ipsum dolor sit amet, consectetur adipiscing elit, sed do eiusmod tempor incididunt ut labore et dolore magna<br>aliqua. Ut enim ad minim veniam, quis nostrud exercitation ullamco laboris nisi ut aliquip ex ea commodo consequat.<br>Duis aute irure dolor in reprehenderit in voluptate velit esse cillum dolore eu fugiat nulla pariatur. Excepteur sint<br>occaecat cupidatat non proident, sunt in culpa</p>
  <div class="btn-navy" style="top:1117px">Read More</div>
</section>

<div class="services-band"></div>
<section class="services">
  <h2 class="abs center section-title" style="top:1288px;font-size:42px">Our Services</h2>
  <p class="abs center lede" style="top:1345px">Lorem ipsum dolor sit amet, consectetur adipiscing elit, sed do<br>eiusmod tempor incididunt ut labore et dolore</p>
  <div class="rule" style="top:1416px"></div>
  <div class="tab-active">Staff Augmentation</div>
  <div class="tab">Operation Support</div>

  <div class="svc-card" style="left:112px;width:303px">
    <div class="svc-photo" role="img" aria-label="Two colleagues shaking hands in an office" style="background:linear-gradient(160deg,#8b95a0,#c9ccd0 55%,#5c6670)"></div>
    <div class="svc-label">SPECIFIC TALENT</div>
  </div>
  <div class="svc-card" style="left:447px;width:305px">
    <div class="svc-photo" role="img" aria-label="Professional woman in glasses at a meeting table" style="background:linear-gradient(160deg,#3b3f48,#8f939a 55%,#4a4d55)"></div>
    <div class="svc-label">ENHANCING</div>
  </div>
  <div class="svc-card" style="left:782px;width:305px">
    <div class="svc-photo" role="img" aria-label="Team discussing ideas in a bright office" style="background:linear-gradient(160deg,#a99888,#d8d2cb 55%,#6d6a6a)"></div>
    <div class="svc-label">BUSINESS CAPABILITIES</div>
  </div>
</section>

<section class="news">
  <h2 class="abs center section-title" style="top:2040px;font-size:42px">Latest News</h2>
  <p class="abs center lede" style="top:2099px">Lorem ipsum dolor sit amet, consectetur adipiscing elit, sed do<br>eiusmod tempor incididunt ut labore et dolore</p>
  <div class="rule" style="top:2167px"></div>

  <article class="news-lead">
    <div class="photo" role="img" aria-label="Light bulb hanging over a team working at a table"></div>
    <div class="pill" style="position:absolute;left:0;top:317px;width:173px;height:36px">Dec 10-2021</div>
    <div style="position:absolute;left:28px;top:380px;width:420px">
      <p class="news-title" style="font-size:16px;line-height:25.5px">Lorem ipsum dolor sit amet, consectetur adipiscing elit, sed do Lorem ipsum dolor sit</p>
      <p class="news-text" style="font-size:13.5px;line-height:25.5px;margin-top:10px">sed do eiusmod tempor incididunt ut labore et dolore magna aliqua. Ut enim ad minim veniam, quis nostrud exercitation ullamco laboris nisi ut aliquip</p>
      <span class="read-more" style="font-size:15px;margin:16px 0 0 5px">Read More ▸</span>
    </div>
  </article>

  <article class="news-item" style="top:2205px">
    <div class="photo" role="img" aria-label="Colleagues reviewing work at a laptop" style="background:linear-gradient(160deg,#8a8c92,#cfd1d4 50%,#6a6560)"></div>
    <div class="body">
      <div class="pill">Dec 10-2021</div>
      <p class="news-title">Lorem ipsum dolor sit amet, consectetur adipiscing elit, sed do</p>
      <p class="news-text">sed do eiusmod tempor incididunt ut labore et dolore magna aliqua. Ut enim ad minim veniam, quis</p>
      <span class="read-more">Read More ▸</span>
    </div>
  </article>
  <article class="news-item" style="top:2509px">
    <div class="photo" role="img" aria-label="Two colleagues talking at an office desk" style="background:linear-gradient(160deg,#7d7a74,#d3cec6 50%,#5f6a60)"></div>
    <div class="body">
      <div class="pill">Dec 10-2021</div>
      <p class="news-title">Lorem ipsum dolor sit amet, consectetur adipiscing elit, sed do</p>
      <p class="news-text">sed do eiusmod tempor incididunt ut labore et dolore magna aliqua. Ut enim ad minim veniam, quis</p>
      <span class="read-more">Read More ▸</span>
    </div>
  </article>

  <div class="btn-navy" style="top:2820px">View More</div>
</section>

<section class="testimonials" role="img" aria-label="Dark office backdrop behind client testimonial">
  <p class="abs center" style="top:76px;font-size:21px;color:#fff;letter-spacing:.5px">TESTIMONIALS</p>
  <p class="abs center" style="top:112px;font-size:24.5px;color:#fff">Lorem ipsum dolor sit amet, consectetur adipiscing elit,</p>
  <p class="abs" style="left:238px;top:164px;font-size:18px;color:#fff;font-weight:700">❝</p>
  <p class="abs center" style="top:180px;font-size:14.5px;line-height:29.5px;font-style:italic;color:#fff">Lorem ipsum dolor sit amet, consectetur adipiscing elit, sed do eiusmod tempor incididunt ut labore et<br>dolore magna aliqua. Ut enim ad minim veniam, quis nostrud exercitationLorem ipsum dolor sit amet,<br>consectetur adipiscing elit, sed do eiusmod tempor incididunt ut labore et dolore magna aliqua. Ut<br>enim ad minim veniam, quis nostrud exercitation</p>
  <p class="abs" style="left:938px;top:268px;font-size:18px;color:#fff;font-weight:700">❞</p>
  <p class="abs center" style="top:316px;font-size:19px;color:#fff">Dana Whitlock.</p>
  <p class="abs center" style="top:348px;font-size:11.5px;color:#fff">Lorem ipsum dolor</p>
</section>
<svg class="arrow" style="left:156px" viewBox="0 0 20 30"><path d="M16 3L4 15l12 12" stroke="#fff" stroke-width="3" fill="none"/></svg>
<svg class="arrow" style="left:1022px" viewBox="0 0 20 30"><path d="M4 3l12 12L4 27" stroke="#fff" stroke-width="3" fill="none"/></svg>
<div class="dots"><span></span><span></span><span></span><span></span><span></span><span></span><span></span><span></span><span></span><span></span></div>

<footer class="site-footer">
  <div class="brand brand-footer"><span class="brand-dot"></span><span class="brand-name">MERIDALE<br>STAFFING</span></div>
  <div class="foot-rule" style="top:320px"></div>
  <p class="abs center" style="top:356px;font-size:15px">© 2022 Meridale Staffing. | All Rights Reserved</p>
</footer>
<span class="social" style="left:114px"></span>
<span class="social" style="left:152px"></span>
<span class="social" style="left:190px"></span>
<span class="social" style="left:229px"></span>
<div class="foot-col" style="left:485px;color:#fff">
  <h4>Quick Links</h4>
  <ul><li>Home</li><li>About Us</li><li>Services</li><li>Blog</li><li>Reviews</li><li>Contact</li></ul>
</div>
<div class="foot-col" style="left:648px;color:#fff">
  <h4>Services</h4>
  <ul><li>Staff Augmentation</li><li>Operation Support.</li></ul>
</div>
<div class="foot-col" style="left:862px;color:#fff;width:280px">
  <h4>Contact Us</h4>
  <ul>
    <li><svg width="10" height="13" viewBox="0 0 10 13"><path d="M5 0a5 5 0 0 0-5 5c0 4 5 8 5 8s5-4 5-8a5 5 0 0 0-5-5z" fill="#fff"/><circle cx="5" cy="5" r="1.8" fill="#0f3a60"/></svg> Lorem ipsum dolor sit amet, consectetur adipiscing</li>
    <li style="margin-top:6px"><svg width="13" height="10" viewBox="0 0 13 10"><rect width="13" height="10" fill="#fff"/><path d="M0 0l6.5 5L13 0" stroke="#0f3a60" fill="none"/></svg> hello@meridalestaffing.com</li>
    <li style="margin-top:6px"><svg width="12" height="12" viewBox="0 0 12 12"><path d="M2 0l3 3-1.5 2a8 8 0 0 0 3.5 3.5L9 7l3 3-2 2C5 12 0 7 0 2z" fill="#fff"/></svg> +1 (555) 014 2270</li>
  </ul>
</div>

</body>
</html>
```